Luxury Real Estate Website, Midwest, United States

We need web design services for a luxury website. We need IDX Integration with our MLS. We want this to be a very simple website with amazing graphics. We want it to link up with our MailChimp account in order to generate leads through a "More Information" Pop up on the main page. We want the main page to be covered with one large graphic that is a rolling slideshow of active listings of $400,000 and up from the IDX Integration. We need this website to give a very exclusive and sleek look. Lots of black is good... I will upload our logos in Black and Silver. We will also need an "About" page that we are going to call "Qeno Info". We want our graphics to be extremely impressive. Keep in mind, we are a company in the Midwest of the United States, and our real estate has a different look than homes in California or Florida. We need graphics that are realistic for the Midwest, yet still high-end.
Target Market(s)
Luxury Homeowners in the Midwest United States. The graphics needs to be pristine.
Industry/Entity Type
Real Estate
Coding
Coded - Design and coding required
Number of Pages Required
3 page
Requirements
Must have
- Large graphics with IDX Integration. The photos of real estate need to represent real estate that is common in the Midwest, United States. We also need MailChimp integration. We need a pop up that is titled "My Free Market Analysis" that makes them fill out a contact form asking for Full Name, Email Address, Phone Number and Address. This needs to be a pop up on the front page and will integrate with our MailChimp account. We also need a page called "About Qe No Home". And another page where clients can download informational PDFs. The main component needs to be a front page search engine connected with the IDX to access active listings from our MLS. I attached our logos and a sample front page of a website. I would love for ours to look similar.
Nice to have
- Lake House photos on midwest lakes are a plus.
Should not have
- Should not have clutter. This website needs to be clean, luxurious and exclusive.

```html
<!DOCTYPE html>
<html lang="en">
<head>
<meta charset="utf-8">
<title>Hearthside Realty Group</title>
<link rel="stylesheet" href="https://fonts.googleapis.com/css2?family=Questrial&family=Open+Sans:wght@400;600&display=swap">
<style>
:root{
  --ink:#111111;
  --charcoal:#2a2a2a;
  --panel:rgba(40,40,40,.82);
  --accent:#c6d4e8;
  --paper:#ffffff;
  --mist:#f0f0f0;
  --shade:#cfcfcf;
  --text:#444444;
  --footer-text:#d8d8d8;
}
*{box-sizing:border-box;margin:0;padding:0}
html,body{width:1200px;height:2459px;overflow:hidden;background:var(--paper)}
body{position:relative;font-family:"Open Sans",Arial,sans-serif;color:var(--text)}
.display{font-family:"Questrial","Century Gothic",sans-serif}
.abs{position:absolute}

/* header */
.site-header{left:0;top:0;width:1200px;height:128px;background:var(--charcoal)}
.brand-box{left:0;top:0;width:360px;height:128px;background:var(--paper);display:flex;align-items:center;justify-content:center;gap:12px}
.brand-mark{width:14px;height:14px;background:var(--ink)}
.brand-name{font-family:"Questrial",sans-serif;font-size:25px;color:var(--ink);letter-spacing:.5px}
.phone{left:888px;top:20px;display:flex;align-items:center;gap:12px;color:#fff;font-family:"Questrial",sans-serif;font-size:25px}
.main-nav{left:464px;top:74px;display:flex;gap:0;font-family:"Questrial",sans-serif;font-size:15px;color:#cfcfcf;text-transform:uppercase}
.main-nav a{color:inherit;text-decoration:none;margin-right:42px}
.main-nav a.current{color:#fff;text-decoration:underline;text-underline-offset:5px}

/* hero */
.hero{left:0;top:128px;width:1200px;height:660px}
.search-panel{left:134px;top:480px;width:933px;height:131px;background:var(--panel)}
.tab{top:483px;height:46px;display:flex;align-items:center;justify-content:center;font-family:"Questrial",sans-serif;font-size:19px;letter-spacing:.5px}
.tab-search{left:275px;width:320px;background:var(--accent);color:#222}
.tab-worth{left:605px;width:318px;background:#333;color:#bdbdbd}
.search-field{left:161px;top:542px;width:878px;height:46px;background:#fff;display:flex;align-items:center;justify-content:space-between;padding:0 20px 0 20px;font-size:17px;color:#333}
.side-btn{left:1126px;width:52px;height:52px;border-radius:50%;background:#2b2b2b;display:flex;align-items:center;justify-content:center}

/* welcome */
.welcome-photo{left:133px;top:849px}
.welcome-copy{left:600px;top:843px;width:470px}
.section-title{font-family:"Questrial",sans-serif;color:var(--ink);font-size:33px;line-height:45px;letter-spacing:.5px;text-transform:uppercase}
.welcome-copy p{margin-top:16px;font-size:11.6px;line-height:18.2px;color:#555}
.btn{display:flex;align-items:center;justify-content:center;background:var(--accent);color:#222;font-family:"Questrial",sans-serif;text-decoration:none}
.read-more{left:600px;top:1121px;width:95px;height:39px;font-size:13px}

/* listings */
.listings-bg{left:0;top:1241px}
.listings-title{left:0;top:1310px;width:1200px;text-align:center}
.listing-card{top:1377px;width:297px;background:#fff}
.listing-photo{width:297px;height:210px}
.listing-caption{height:80px;display:flex;align-items:center;justify-content:center;text-align:center;padding:0 20px;font-family:"Questrial",sans-serif;font-size:15px;line-height:22px;color:#444}
.view-all{left:552px;top:1695px;width:95px;height:37px;font-size:13px}

/* downloads */
.downloads-title{left:0;top:1975px;width:1200px;text-align:center}
.downloads-text{left:135px;top:2025px;width:930px;text-align:center;font-size:11.6px;line-height:21px;color:#555}
.download-btn{left:464px;top:2096px;width:272px;height:46px;font-size:15px;letter-spacing:.3px;text-transform:uppercase}

/* footer */
.footer-bg{left:0;top:2220px}
.footer-brand{left:133px;top:2326px;display:flex;align-items:center;gap:10px}
.footer-brand .brand-mark{background:#8a8a8a;width:10px;height:10px}
.footer-brand .brand-name{color:#8a8a8a;font-size:20px}
.footer-nav{left:133px;top:2383px;font-size:11.5px;color:var(--footer-text)}
.footer-nav span{margin:0 9px;color:#888}
.copyright{left:133px;top:2414px;font-size:11.5px;color:var(--footer-text)}
.social{top:2388px;width:40px;height:40px;background:#fff;transform:rotate(45deg)}
</style>
</head>
<body>

<header class="site-header abs">
  <div class="brand-box abs">
    <span class="brand-mark"></span>
    <span class="brand-name">HEARTHSIDE REALTY</span>
  </div>
  <div class="phone abs">
    <svg width="22" height="22" viewBox="0 0 24 24" aria-hidden="true"><path fill="#fff" d="M6.6 10.8a15.2 15.2 0 0 0 6.6 6.6l2.2-2.2a1 1 0 0 1 1-.25 11.4 11.4 0 0 0 3.6.57 1 1 0 0 1 1 1V20a1 1 0 0 1-1 1A17 17 0 0 1 3 4a1 1 0 0 1 1-1h3.5a1 1 0 0 1 1 1c0 1.25.2 2.45.57 3.6a1 1 0 0 1-.25 1z"/></svg>
    <span>555 014 2290</span>
  </div>
  <nav class="main-nav abs">
    <a class="current" href="#">Home</a>
    <a href="#">Qeno Info</a>
    <a href="#">About Qe No Home</a>
    <a href="#">Downloads</a>
    <a href="#">Contact Us</a>
  </nav>
</header>

<svg class="hero abs" width="1200" height="660" viewBox="0 0 1200 660">
  <defs>
    <linearGradient id="lakeScene" x1="0" y1="0" x2="0" y2="1">
      <stop offset="0" stop-color="#8fb4e6"/>
      <stop offset=".38" stop-color="#a9c6ea"/>
      <stop offset=".5" stop-color="#b86a35"/>
      <stop offset=".6" stop-color="#4d6b3a"/>
      <stop offset=".72" stop-color="#3f7fb3"/>
      <stop offset="1" stop-color="#2f6fa8"/>
    </linearGradient>
  </defs>
  <polygon points="0,0 1200,0 1200,454 287,634 0,478" fill="var(--ink)" transform="translate(0,0)"/>
  <polygon points="0,0 1200,0 1200,454 287,634 0,478" fill="#2d2d2d" transform="translate(0,12)" opacity=".9"/>
  <polygon role="img" aria-label="Photograph of an orange-shingled lake house with a dock, lamp posts and calm water" points="0,0 1200,0 1200,454 287,616 0,470" fill="url(#lakeScene)"/>
</svg>

<div class="search-panel abs"></div>
<div class="tab tab-search abs">SEARCH HOMES</div>
<div class="tab tab-worth abs">WHAT’S YOUR HOME WORTH</div>
<div class="search-field abs">
  <span>Search homes by city &amp; state, Zip... etc</span>
  <svg width="16" height="16" viewBox="0 0 16 16" aria-hidden="true"><circle cx="6.5" cy="6.5" r="4.8" fill="none" stroke="#222" stroke-width="2"/><line x1="10" y1="10" x2="14.5" y2="14.5" stroke="#222" stroke-width="2.4"/></svg>
</div>
<div class="side-btn abs" style="top:313px">
  <svg width="22" height="20" viewBox="0 0 22 20" aria-hidden="true"><ellipse cx="11" cy="9" rx="10" ry="7.5" fill="#fff"/><polygon points="4,13 3,19 9,15" fill="#fff"/></svg>
</div>
<div class="side-btn abs" style="top:375px">
  <svg width="22" height="22" viewBox="0 0 24 24" aria-hidden="true"><polygon fill="#fff" points="12,2 15,9 22,9.3 16.5,14 18.5,21 12,17 5.5,21 7.5,14 2,9.3 9,9"/></svg>
</div>

<svg class="welcome-photo abs" width="440" height="312" viewBox="0 0 440 312">
  <defs>
    <linearGradient id="poolScene" x1="0" y1="0" x2="1" y2="1">
      <stop offset="0" stop-color="#c9dde8"/>
      <stop offset=".45" stop-color="#7fa3bc"/>
      <stop offset=".75" stop-color="#3a4a5a"/>
      <stop offset="1" stop-color="#35c6de"/>
    </linearGradient>
  </defs>
  <polygon points="340,0 363,0 440,156 363,312 340,312 417,156" fill="var(--shade)"/>
  <polygon role="img" aria-label="Photograph of a modern white villa with an illuminated pool at dusk" points="0,0 330,0 406,156 330,312 0,312" fill="url(#poolScene)"/>
</svg>

<div class="welcome-copy abs">
  <h1 class="section-title">Welcome to<br>Hearthside Realty Group</h1>
  <p>Pellentesque a imperdiet dolor, et auctor est. Fusce sollicitudin lorem et luctus volutpat. Proin placerat dapibus gravida. In tristique tristique nulla eget hendrerit. Maecenas vel tortor accumsan quam varius imperdiet vel eget elit. Aenean facilisis tincidunt lectus, id dictum nisi luctus eget. Vivamus efficitur ex condimentum, malesuada eros eget, feugiat nibh. Sed tellus ex, imperdiet eget gravida sit amet, volutpat eget turpis. In nec ultricies est. Etiam mattis augue vehicula odio posuere, sit amet tempus lectus luctus. Nulla facilisi. Etiam vel massa elementum, bibendum tellus venenatis, feugiat massa. Curabitur venenatis lacinia ornare.</p>
</div>
<a class="btn read-more abs" href="#">Read More</a>

<svg class="listings-bg abs" width="1200" height="650" viewBox="0 0 1200 650">
  <polygon points="0,496 901,628 1200,496 1200,510 920,648 0,500" fill="var(--shade)"/>
  <polygon points="0,0 1200,0 1200,496 901,628 0,496" fill="var(--mist)"/>
</svg>
<h2 class="section-title listings-title abs">Home Listings</h2>

<article class="listing-card abs" style="left:133px">
  <div class="listing-photo" role="img" aria-label="Photograph of a lit lakeside mansion at twilight" style="background:linear-gradient(180deg,#5a86c4 0%,#3d5f8f 45%,#b0743a 70%,#4a3e63 100%)"></div>
  <div class="listing-caption">Pellentesque convallis molestie enim sit amet efficitur</div>
</article>
<article class="listing-card abs" style="left:451px">
  <div class="listing-photo" role="img" aria-label="Photograph of a stone manor house with a formal lawn" style="background:linear-gradient(180deg,#6f9ed6 0%,#c9b08a 40%,#a28a66 62%,#4f8a3a 100%)"></div>
  <div class="listing-caption">Vivamus lacus justo, ultrices nec erat in, euismod</div>
</article>
<article class="listing-card abs" style="left:770px">
  <div class="listing-photo" role="img" aria-label="Photograph of a waterfront patio house beside a lake" style="background:linear-gradient(180deg,#4f8ee0 0%,#d8c8a8 45%,#2f7fb8 70%,#a89070 100%)"></div>
  <div class="listing-caption">Vivamus eleifend vitae nulla vel malesuada</div>
</article>
<a class="btn view-all abs" href="#">View All</a>

<h2 class="section-title downloads-title abs">Downloads</h2>
<p class="downloads-text abs">Aenean sed quam non sapien faucibus consequat vitae sit amet orci. Praesent quis risus mi. In mollis nulla in pulvinar dictum. Vivamus interdum sagittis felis, ut dapibus ligula feugiat ac. In dictum sapien eu tellus finibus fermentum. Aenean faucibus lacus ut mollis commodo. Donec vestibulum odio sem, ac laoreet massa ullamcorper id. Donec molestie nisi et tellus hendrerit vehicula. Nunc eu ligula sed quam pulvinar maximus in vitae eros.</p>
<a class="btn download-btn abs" href="#">Download our PDF Broucher</a>

<svg class="footer-bg abs" width="1200" height="239" viewBox="0 0 1200 239">
  <polygon points="0,80 287,4 1200,155 1200,239 0,239" fill="#2c2c2c"/>
  <polygon points="0,96 287,22 1200,158 1200,239 0,239" fill="#000"/>
</svg>
<div class="footer-brand abs">
  <span class="brand-mark"></span>
  <span class="brand-name">HEARTHSIDE REALTY</span>
</div>
<nav class="footer-nav abs">Home<span>|</span>Qeno Info<span>|</span>About Qe No Home<span>|</span>Downloads<span>|</span>Contact us</nav>
<p class="copyright abs">Copyright © 2018 Hearthside Realty Group. All rights reserved.</p>
<div class="social abs" style="left:893px" aria-label="Social link"></div>
<div class="social abs" style="left:957px" aria-label="Social link"></div>
<div class="social abs" style="left:1019px" aria-label="Social link"></div>

</body>
</html>
```